Business Card Design for my Real Estate Investing Company

This is for a Real Estate Investing Company that will be serving the Las Vegas Valley. Id like the following slogan included: "Investing in Our Community" I have attached my logo. You will see the color tones I'm interested in..in my logo. I would like the card to be double-sided with a modern, professional look.
Target Market(s)
Homeowners, banks, real estate industry
Industry/Entity Type
Real Estate
Contact Information for Business Card
name: Dale Harwick
position: Managing Member
address: 4821 Corliss Pkwy ste 207-300
N. Las Vegas, NV 89084
phone: (702) 555-0143
fax: (702) 555-0187
email: SummitRidgeEstate@hollowmail.test
web: SummitRidgeEstates.test
*At the bottom of the card I would like....
We buy houses for cash....no repairs, no commissions, no fees!
Logo Text
SUMMIT RIDGE ESTATES "Investing in Our Community"
Font styles to use
Other font styles liked:
- Lora
Requirements
Must have
- On the back of the card, i'd like to have my logo large and the following statements:
- Are you considering selling your home? Want a simple, hassle-free transaction? We can help! We buy houses for cash and can close quickly! No need to do any repairs, no realtor commissions, no closing costs.....and no headaches. Let us help you with your real estate needs...!
Nice to have
- multiple colors 2 two tone on front and back

```html
<!DOCTYPE html>
<html lang="en">
<head>
<meta charset="utf-8">
<title>Summit Ridge Estates – Business Card</title>
<link rel="stylesheet" href="https://fonts.googleapis.com/css2?family=Lora:ital,wght@0,400;0,700;1,400&family=Montserrat:wght@400;500&family=Oswald:wght@500&display=swap">
<style>
  :root {
    --stage: #2b2b2d;
    --card: #050505;
    --brand-blue: #1f5fc0;
    --band-blue: #1d5bb8;
    --silver: #9a9a9a;
    --white: #ffffff;
    --rule: #8a8a8a;
  }
  * { box-sizing: border-box; margin: 0; padding: 0; }
  html, body {
    width: 1200px; height: 900px; overflow: hidden;
    background: var(--stage);
  }
  .stage {
    position: relative; width: 1200px; height: 900px;
  }
  .card {
    position: absolute; left: 260px;
    width: 680px; height: 400px;
    background: var(--card);
    border-radius: 22px;
    overflow: hidden;
    color: var(--white);
    box-shadow: 0 18px 40px rgba(0,0,0,.45);
  }
  .card--back { top: 40px; }
  .card--front { top: 470px; }

  /* Back side */
  .brand {
    position: absolute; top: 62px; left: 0; right: 0;
    text-align: center;
  }
  .brand__name {
    display: inline-flex; align-items: center; gap: 14px;
    font-family: "Lora", serif; font-weight: 700;
    font-size: 40px; letter-spacing: 1px;
    color: var(--brand-blue);
  }
  .brand__mark {
    width: 26px; height: 26px; background: var(--silver);
  }
  .brand__slogan {
    margin-top: 10px;
    font-family: "Lora", serif; font-size: 17px;
    letter-spacing: 5px; color: var(--white);
  }
  .pitch {
    position: absolute; top: 200px; left: 40px; right: 40px;
    text-align: center;
    font-family: "Montserrat", sans-serif; font-size: 17px;
    line-height: 1.5; color: var(--white);
  }

  /* Front side */
  .front-brand {
    position: absolute; left: 40px; top: 140px; width: 250px;
    display: flex; align-items: center; gap: 12px;
    font-family: "Lora", serif; font-weight: 700; font-size: 26px;
    line-height: 1.1; color: var(--brand-blue);
  }
  .front-brand .brand__mark { flex: none; width: 34px; height: 34px; }
  .divider {
    position: absolute; left: 300px; top: 70px; width: 1px; height: 210px;
    background: linear-gradient(var(--card), var(--rule), var(--card));
    transform: rotate(-12deg);
  }
  .contact {
    position: absolute; left: 345px; top: 48px;
    font-family: "Montserrat", sans-serif; font-size: 15px; line-height: 1.45;
  }
  .contact__name {
    font-family: "Lora", serif; font-size: 25px; color: var(--brand-blue);
    letter-spacing: 1px; line-height: 1.2;
  }
  .contact__title { margin-bottom: 4px; }
  .contact__list { list-style: none; margin-top: 6px; }
  .contact__list li { display: flex; align-items: center; gap: 10px; }
  .contact__icon { width: 13px; height: 13px; fill: var(--brand-blue); flex: none; }
  .contact__accent { color: var(--brand-blue); }
  .offer-band {
    position: absolute; left: 0; right: 0; bottom: 26px; height: 34px;
    display: flex;
  }
  .offer-band__end { width: 60px; background: var(--white); }
  .offer-band__text {
    flex: 1; background: var(--band-blue);
    border: 2px solid var(--white);
    display: flex; align-items: center; justify-content: center;
    font-family: "Oswald", sans-serif; font-weight: 500; font-size: 17px;
    letter-spacing: .5px; color: var(--white);
  }
</style>
</head>
<body>
<main class="stage">

  <section class="card card--back" aria-label="Card back">
    <div class="brand">
      <div class="brand__name"><span class="brand__mark"></span>SUMMIT RIDGE ESTATES</div>
      <p class="brand__slogan">“Investing in Our Community”</p>
    </div>
    <p class="pitch">
      Are you considering selling your home?<br>
      Want a simple, hassle-free transaction?<br>
      We can help! We buy houses for cash and can close quickly!<br>
      No need to do any repairs, no realtor commissions, no closing costs<br>
      and no headaches. Let us help you with your real estate needs...!
    </p>
  </section>

  <section class="card card--front" aria-label="Card front">
    <div class="front-brand"><span class="brand__mark"></span>SUMMIT RIDGE ESTATES</div>
    <div class="divider"></div>
    <div class="contact">
      <h1 class="contact__name">DALE HARWICK</h1>
      <p class="contact__title">Managing Member</p>
      <p>4821 Corliss Pkwy ste 207-300<br>N. Las Vegas, NV 89084</p>
      <ul class="contact__list">
        <li><svg class="contact__icon" viewBox="0 0 24 24"><path d="M6.6 10.8a15.1 15.1 0 0 0 6.6 6.6l2.2-2.2a1 1 0 0 1 1-.25 11.4 11.4 0 0 0 3.6.57 1 1 0 0 1 1 1V20a1 1 0 0 1-1 1A17 17 0 0 1 3 4a1 1 0 0 1 1-1h3.5a1 1 0 0 1 1 1c0 1.25.2 2.45.57 3.57a1 1 0 0 1-.25 1z"/></svg>(702) 555-0143</li>
        <li><svg class="contact__icon" viewBox="0 0 24 24"><path d="M6 2h12v6H6zM3 9h18v9h-3v4H6v-4H3zm5 6v5h8v-5z"/></svg>(702) 555-0187</li>
        <li><svg class="contact__icon" viewBox="0 0 24 24"><path d="M2 5h20v14H2zm2 2v.5l8 5 8-5V7zm0 2.8V17h16V9.8l-8 5z"/></svg>SummitRidgeEstate@hollowmail.test</li>
        <li><svg class="contact__icon" viewBox="0 0 24 24"><path d="M12 2a10 10 0 1 0 0 20 10 10 0 0 0 0-20zm0 2c.9 1.2 1.6 2.6 2 4h-4c.4-1.4 1.1-2.8 2-4zM4.3 14a8 8 0 0 1 0-4h3.4a16 16 0 0 0 0 4zm.9 2h3c.4 1.4 1 2.7 1.8 3.8A8 8 0 0 1 5.2 16zm3-8h-3A8 8 0 0 1 10 4.2 14 14 0 0 0 8.2 8zM12 20c-.9-1.2-1.6-2.6-2-4h4c-.4 1.4-1.1 2.8-2 4zm2.3-6H9.7a14 14 0 0 1 0-4h4.6a14 14 0 0 1 0 4zm-.3 5.8c.8-1.1 1.4-2.4 1.8-3.8h3A8 8 0 0 1 14 19.8zM16.3 14a16 16 0 0 0 0-4h3.4a8 8 0 0 1 0 4z"/></svg>www.<span class="contact__accent">SummitRidgeEstates</span>.test</li>
      </ul>
    </div>
    <div class="offer-band">
      <span class="offer-band__end"></span>
      <p class="offer-band__text">WE BUY HOUSES FOR CASH....NO REPAIRS, NO COMMISSIONS, NO FEES!</p>
      <span class="offer-band__end"></span>
    </div>
  </section>

</main>
</body>
</html>
```